Promotional business a5 Notepad design

I am looking for a custom a5 notepad design as a promotional item to give away to customers etc.
Attached will be a desk planner we had designed feel free to use as a reference.
We want the notepad to have lines running horizontal not squares like the desk planner example.

Industry/Entity Type

Hydraulic / industrial

Colors

Designer to choose colors to be used in the design.

```html
<!DOCTYPE html>
<html lang="en">
<head>
<meta charset="utf-8">
<title>Meridian Hose &amp; Couplings — A5 Notepad</title>
<link rel="stylesheet" href="https://fonts.googleapis.com/css2?family=Poppins:wght@400;600&display=swap">
<style>
  :root {
    --backdrop: #d9dadb;
    --paper: #ffffff;
    --brand-blue: #1a2fbf;
    --ink: #111111;
    --text-grey: #4a4a4a;
    --rule: #1a1a1a;
  }
  * { margin: 0; padding: 0; box-sizing: border-box; }
  html, body {
    width: 973px; height: 1200px; overflow: hidden;
    background: var(--backdrop);
    font-family: "Poppins", sans-serif;
  }
  .notepad {
    position: absolute; left: 62px; top: 0;
    width: 848px; height: 1200px;
    background: var(--paper);
  }
  .brand {
    position: absolute; left: 67px; top: 92px;
    display: flex; align-items: center; gap: 10px;
  }
  .brand-dot {
    width: 38px; height: 38px; border-radius: 50%;
    background: var(--ink);
  }
  .brand-name {
    font-weight: 600; font-size: 21px; color: var(--brand-blue);
    letter-spacing: 0.2px; white-space: nowrap;
  }
  .contact {
    position: absolute; left: 564px; top: 66px;
    font-size: 14.5px; line-height: 17.5px; color: var(--text-grey);
    font-weight: 400;
  }
  .contact .address { margin-bottom: 8px; }
  .contact .row { display: flex; align-items: center; gap: 9px; }
  .contact .row svg { width: 13px; height: 13px; fill: var(--brand-blue); flex: none; }
  .rules { position: absolute; left: 70px; top: 0; width: 710px; height: 1100px; }
  .rule {
    position: absolute; left: 0; width: 710px; height: 1.5px;
    background: var(--rule);
  }
  .band-blue {
    position: absolute; left: 0; top: 1166px; width: 100%; height: 13px;
    background: var(--brand-blue);
  }
  .band-black {
    position: absolute; left: 0; top: 1183px; width: 100%; height: 17px;
    background: var(--ink);
  }
</style>
</head>
<body>
  <main class="notepad">
    <header>
      <div class="brand">
        <span class="brand-dot"></span>
        <span class="brand-name">Meridian Hose &amp; Couplings</span>
      </div>
      <address class="contact" style="font-style:normal">
        <div class="address">2140 Harbor Ridge Road<br>Portside, Alaska 99512</div>
        <div class="row">
          <svg viewBox="0 0 24 24" aria-hidden="true"><path d="M6.6 10.8a15.1 15.1 0 0 0 6.6 6.6l2.2-2.2c.3-.3.7-.4 1-.2 1.1.4 2.3.6 3.6.6.6 0 1 .4 1 1V20c0 .6-.4 1-1 1A17 17 0 0 1 3 4c0-.6.4-1 1-1h3.5c.6 0 1 .4 1 1 0 1.3.2 2.5.6 3.6.1.3 0 .7-.2 1z"/></svg>
          <span>555-014-2287</span>
        </div>
        <div class="row">
          <svg viewBox="0 0 24 24" aria-hidden="true"><path d="M2 5h20v14H2z M4 7v.4l8 5.2 8-5.2V7z" fill-rule="evenodd"/></svg>
          <span>hello@meridianhose.com</span>
        </div>
        <div class="row">
          <svg viewBox="0 0 24 24" aria-hidden="true"><circle cx="12" cy="12" r="10"/><path d="M12 4a8 8 0 0 0-6 3c1.5.5 2 2 3.5 2s1 2 2.5 2.5c1 .4 0 3 1.5 3.5.8-2 3-2 3-4s-2-1.5-2.5-3S16 5.5 12 4z" fill="#ffffff"/></svg>
          <span>www.meridianhose.com</span>
        </div>
      </address>
    </header>
    <section class="rules" aria-label="Writing lines">
      <div class="rule" style="top:222px"></div>
      <div class="rule" style="top:285px"></div>
      <div class="rule" style="top:348px"></div>
      <div class="rule" style="top:412px"></div>
      <div class="rule" style="top:474px"></div>
      <div class="rule" style="top:538px"></div>
      <div class="rule" style="top:600px"></div>
      <div class="rule" style="top:664px"></div>
      <div class="rule" style="top:727px"></div>
      <div class="rule" style="top:790px"></div>
      <div class="rule" style="top:853px"></div>
      <div class="rule" style="top:917px"></div>
      <div class="rule" style="top:979px"></div>
      <div class="rule" style="top:1041px"></div>
    </section>
    <footer>
      <div class="band-blue"></div>
      <div class="band-black"></div>
    </footer>
  </main>
</body>
</html>
```